Detail Shop Business card design

i need a business card design for my new detailing company called 'Brisk's Polish Works'. i want an all black and white design . simple, direct and to the point. i want the designer to choose a fitting font to match the logothe front should have logo, address, phone and email and the back side should have a slogan and text indicating that we offer services on anything including cars, trucks, motorcycles and RVs. slogan will read "we take pride in your ride"
maybe also very small on the back side the IG icon with Brisks_Polish_Works

phone 208.417.6352
address 3847 E Larkin Ave
Spokane WA 99214
email: BrisksPolish@mailvexo.com

Target Market(s)

all ages , auto enthusiasts

Industry/Entity Type

Automotive

Contact Information for Business Card

the front should have logo, address, phone and email and the back side should have a slogan and text indicating that we offer services on anything including cars, trucks, motorcycles and RVs. slogan will read "we take pride in your ride"

phone 208.417.6352
address 3847 E Larkin Ave
Spokane WA 99214

Colors
000000
ffffff

Requirements
Must have
• bold font and very simple design with good spacing
Nice to have
• anything creative from the designer indicating we service any types of vehicles
Should not have
• any colors ,

```html
<!DOCTYPE html>
<html lang="en">
<head>
<meta charset="utf-8">
<title>Brisk's Polish Works – Business Card</title>
<link href="https://fonts.googleapis.com/css2?family=Oswald:wght@500;600&family=Roboto:wght@400;700&display=swap" rel="stylesheet">
<style>
  :root {
    --backdrop: #1f1f1f;
    --card: #f7f7f7;
    --ink: #111111;
    --ink-soft: #444444;
    --ink-muted: #555555;
  }
  * { margin: 0; padding: 0; box-sizing: border-box; }
  html, body { width: 1200px; height: 960px; overflow: hidden; }
  body { background: var(--backdrop); position: relative; font-family: "Roboto", Arial, sans-serif; }

  .card {
    position: absolute;
    width: 600px;
    height: 343px;
    background: var(--card);
    box-shadow: 0 2px 6px rgba(0,0,0,.5);
  }
  .card--front { left: 314px; top: 113px; }
  .card--back  { left: 311px; top: 472px; }

  /* Front */
  .identity {
    position: absolute;
    right: 74px;
    top: 50px;
    text-align: right;
  }
  .identity__name {
    font-family: "Oswald", "Arial Narrow", sans-serif;
    font-weight: 500;
    font-size: 46px;
    line-height: 1;
    letter-spacing: -0.5px;
    color: var(--ink);
    transform: scaleX(0.88);
    transform-origin: right;
  }
  .identity__role {
    font-size: 15px;
    color: var(--ink-muted);
    margin-top: 2px;
    letter-spacing: 0.3px;
  }
  .identity__bar {
    position: absolute;
    right: 53px;
    top: 52px;
    width: 6px;
    height: 63px;
    background: var(--ink);
  }

  .contact-list {
    position: absolute;
    left: 48px;
    top: 226px;
    list-style: none;
  }
  .contact-list li {
    display: flex;
    align-items: center;
    height: 19px;
    font-size: 14.5px;
    color: var(--ink-soft);
  }
  .contact-list svg { width: 14px; height: 14px; margin-right: 13px; fill: var(--ink); }

  .address {
    position: absolute;
    right: 53px;
    top: 264px;
    text-align: right;
    font-size: 14.5px;
    line-height: 19px;
    color: var(--ink-soft);
    font-style: normal;
  }

  /* Back */
  .brand-mark {
    position: absolute;
    left: 0; right: 0;
    top: 120px;
    display: flex;
    justify-content: center;
    align-items: center;
    gap: 12px;
  }
  .brand-mark__dot { width: 18px; height: 18px; border-radius: 50%; background: var(--ink); }
  .brand-mark__name {
    font-family: "Oswald", "Arial Narrow", sans-serif;
    font-weight: 600;
    font-size: 34px;
    color: var(--ink);
    text-transform: uppercase;
    letter-spacing: 1px;
  }
  .slogan {
    position: absolute;
    left: 137px;
    width: 324px;
    top: 271px;
    text-align: center;
    font-weight: 700;
    font-size: 17px;
    color: var(--ink);
    padding-bottom: 2px;
    border-bottom: 2px solid var(--ink);
  }
  .services {
    position: absolute;
    left: 0; right: 0;
    top: 297px;
    text-align: center;
    font-family: "Oswald", "Arial Narrow", sans-serif;
    font-weight: 500;
    font-size: 14px;
    color: var(--ink);
  }
</style>
</head>
<body>
  <section class="card card--front">
    <div class="identity">
      <div class="identity__name">DALE MERCER</div>
      <div class="identity__role">CEO/FOUNDER</div>
    </div>
    <div class="identity__bar"></div>

    <ul class="contact-list">
      <li>
        <svg viewBox="0 0 24 24"><path d="M6.6 10.8a15.1 15.1 0 0 0 6.6 6.6l2.2-2.2c.3-.3.7-.4 1-.2 1.1.4 2.3.6 3.6.6.6 0 1 .4 1 1V20c0 .6-.4 1-1 1A17 17 0 0 1 3 4c0-.6.4-1 1-1h3.5c.6 0 1 .4 1 1 0 1.3.2 2.5.6 3.6.1.3 0 .7-.2 1z"/></svg>
        208.417.6352
      </li>
      <li>
        <svg viewBox="0 0 24 24"><path d="M7 1h10a2 2 0 0 1 2 2v18a2 2 0 0 1-2 2H7a2 2 0 0 1-2-2V3a2 2 0 0 1 2-2zm0 3v15h10V4zm5 16.2a1 1 0 1 0 0 2 1 1 0 0 0 0-2z"/></svg>
        836 512 7480
      </li>
      <li>
        <svg viewBox="0 0 24 24"><path d="M2 5h20v2.2l-10 6.3L2 7.2zm0 4.5 10 6.3 10-6.3V19H2z"/></svg>
        BrisksPolish@mailvexo.com
      </li>
      <li>
        <svg viewBox="0 0 24 24"><path d="M12 2a10 10 0 1 0 0 20 10 10 0 0 0 0-20zm-1 17.9A8 8 0 0 1 4.1 10L9 15v1a2 2 0 0 0 2 2zm6.9-2.5A2 2 0 0 0 16 16h-1v-3a1 1 0 0 0-1-1H8v-2h2a1 1 0 0 0 1-1V7h2a2 2 0 0 0 2-2v-.4a8 8 0 0 1 2.9 12.8z"/></svg>
        www.briskspolish.com
      </li>
    </ul>

    <address class="address">
      3847 E Larkin Ave<br>
      Spokane WA 99214
    </address>
  </section>

  <section class="card card--back">
    <div class="brand-mark">
      <span class="brand-mark__dot"></span>
      <span class="brand-mark__name">Brisk's Polish Works</span>
    </div>
    <div class="slogan">WE TAKE PRIDE IN YOUR RIDE</div>
    <div class="services">we offer services on anything including cars, trucks, motorcycles &amp; RVs</div>
  </section>
</body>
</html>
```